Business Card Design - Photographer

I am a landscape photographer and I require a business card design. 

I require two designs:
1)  a double sided business card
 and
b)  a single sided business card 

The single sided design can either be the same as the double sided (with just one side having all the information)....or it can be an entire new design. Its up to you.

My corporate colours are (CMYK):

Blue   69, 32, 0, 0
Grey  72,  64,  47,  31
Green  32,  2,  91,  0
Yellow   0, 19, 92, 0
Orange  0, 39, 75, 0

Colour space in final file should be in CMYK.

The details that need to be included on the card:

- Use the provided Logo
- Name: Wiktor Baranowski
- Email:   sales@vistalumeworks.com.au
- Website:    vistalumeworks.com.au
- Twitter:    chirpline.com/vistalumeworks
- Facebook:   friendsphere.com/vistalumeworks
- Mobile  0417 539 662

Please use the attached template to design the logo to the specified size, including the marked bleed lines. I have also attached my logo in PNG (transparent background) and ai format for you to use.

The final file should be:
- Photoshop version with layers so I can edit the name/text etc. All non vector files should be high resolution at 1039 x 697 pixels at 300 dpi.

I also require a file as:
- Vector based PDF

Anyway questions please contact me.

Thank you

Industry/Entity Type

Landscape

Logo styles of interest
Pictorial/Combination Logo
Abstract Logo
Wordmark Logo
Lettermark Logo
Requirements
Must have
• The details that need to be included on the card:

- Use the provided Logo
- Name: Wiktor Baranowski
- Email: sales@vistalumeworks.com.au
- Website: vistalumeworks.com.au
- Twitter: chirpline.com/vistalumeworks
- Facebook: friendsphere.com/vistalumeworks
- Mobile 0417 539 662

```html
<!DOCTYPE html>
<html lang="en">
<head>
<meta charset="utf-8">
<title>Vistalume Works – Business Cards</title>
<link rel="stylesheet" href="https://fonts.googleapis.com/css2?family=Cinzel:wght@600&family=Open+Sans:wght@400;700&display=swap">
<style>
  :root {
    --backdrop: #2e3436;
    --card: #ffffff;
    --brand-grey: #3b3e50;
    --ink: #000000;
    --text: #2a2a2a;
  }
  * { margin: 0; padding: 0; box-sizing: border-box; }
  html, body { width: 987px; height: 1200px; overflow: hidden; }
  body {
    position: relative;
    background: var(--backdrop);
    font-family: "Open Sans", Arial, sans-serif;
    color: var(--text);
  }
  .card {
    position: absolute;
    left: 90px;
    width: 789px;
    height: 451px;
    background: var(--card);
    border-radius: 28px;
    text-align: center;
  }
  .card--front { top: 100px; }
  .card--back { top: 637px; left: 92px; }

  .brand-mark { position: absolute; left: 50%; transform: translateX(-50%); }
  .brand-name {
    position: absolute;
    left: 0; right: 0;
    font-family: "Cinzel", Georgia, serif;
    font-weight: 600;
    color: var(--brand-grey);
    letter-spacing: 1px;
    line-height: 1;
  }

  .card--front .brand-mark { top: 32px; }
  .card--front .brand-name { top: 194px; font-size: 38px; }

  .holder {
    position: absolute;
    left: 0; right: 0; top: 284px;
    color: var(--ink);
    line-height: 1;
  }
  .holder__name { font-size: 28px; font-weight: 700; }
  .holder__dash { font-size: 24px; padding: 0 4px; }
  .holder__role { font-size: 18px; }

  .contact {
    position: absolute;
    left: 0; right: 0; top: 340px;
    font-size: 18px;
    line-height: 30px;
    color: var(--text);
  }
  .contact b { font-weight: 700; }
  .contact .sep { padding: 0 8px; }

  .card--back .brand-mark { top: 30px; }
  .card--back .brand-name { top: 262px; font-size: 54px; }
  .card--back .site {
    position: absolute;
    left: 0; right: 0; top: 395px;
    font-size: 25px;
    color: var(--brand-grey);
  }
</style>
</head>
<body>
  <section class="card card--front">
    <svg class="brand-mark" width="144" height="144" viewBox="0 0 144 144" aria-hidden="true">
      <circle cx="72" cy="72" r="72" fill="var(--brand-grey)"/>
    </svg>
    <div class="brand-name">VISTALUME WORKS</div>
    <div class="holder">
      <span class="holder__name">Your Name</span><span class="holder__dash">-</span><span class="holder__role">Adminsitrator</span>
    </div>
    <div class="contact">
      <div><b>m</b> : 0417 539 662</div>
      <div><b>e</b> : sales@vistalumeworks.com.au<span class="sep">|</span><b>w</b> : vistalumeworks.com.au</div>
      <div><b>t</b> : chirpline.com/vistalumeworks<span class="sep">|</span><b>f</b> : friendsphere.com/vistalumeworks</div>
    </div>
  </section>

  <section class="card card--back">
    <svg class="brand-mark" width="210" height="210" viewBox="0 0 210 210" aria-hidden="true">
      <circle cx="105" cy="105" r="105" fill="var(--brand-grey)"/>
    </svg>
    <div class="brand-name">VISTALUME WORKS</div>
    <div class="site">www.vistalumeworks.com.au</div>
  </section>
</body>
</html>
```